Business Card Design

New business card design

Target Market(s)

Residential & Commercial Property Managers

Industry/Entity Type

Plumbing Services

Contact Information for Business Card

Name - Rowan Keddle, title - Director, Phone Number - 0431 286 517, email - rowan@tbk-plumbing.com.au, Company ABN - 73 215 904 386,

Font styles to use
Sans Serif

Colors
0054AA
0677BA
7BADD7
CADEEF
E8F1F8

```html
<!DOCTYPE html>
<html lang="en">
<head>
<meta charset="utf-8">
<title>TBK Plumbing Services – Business Card</title>
<link href="https://fonts.googleapis.com/css2?family=Arimo:wght@400;700&display=swap" rel="stylesheet">
<style>
  :root {
    --bg: #eeeeee;
    --ink: #1e232b;
    --blue: #1aa3e8;
    --white: #ffffff;
    --grey-text: #555a62;
  }
  html, body {
    margin: 0;
    padding: 0;
    width: 1200px;
    height: 900px;
    overflow: hidden;
    background: var(--bg);
    font-family: "Arimo", Arial, sans-serif;
  }
  .stage {
    position: relative;
    width: 1200px;
    height: 900px;
  }
  .card {
    position: absolute;
    top: 170px;
    width: 330px;
    height: 560px;
    border-radius: 22px;
    overflow: hidden;
    box-sizing: border-box;
    border: 5px solid var(--blue);
    box-shadow: 0 10px 24px rgba(0,0,0,0.18);
  }
  .card--front { left: 240px; background: var(--white); }
  .card--back  { left: 630px; background: var(--ink); }

  .card__art {
    position: absolute;
    inset: 0;
    width: 100%;
    height: 100%;
  }

  .brand {
    position: absolute;
    display: flex;
    align-items: center;
    gap: 9px;
    font-weight: 400;
    letter-spacing: 0.5px;
    white-space: nowrap;
  }
  .brand__dot {
    width: 11px;
    height: 11px;
    border-radius: 50%;
    background: var(--blue);
    flex: none;
  }
  .card--front .brand { left: 30px; top: 62px; font-size: 23px; color: var(--ink); }
  .card--back .brand  { left: 50%; top: 42%; transform: translate(-50%, -50%); font-size: 23px; color: var(--white); }

  .holder {
    position: absolute;
    right: 26px;
    top: 272px;
    text-align: right;
  }
  .holder__name {
    margin: 0;
    font-size: 20px;
    font-weight: 700;
    color: var(--blue);
    text-transform: uppercase;
    white-space: nowrap;
  }
  .holder__role {
    margin: 3px 0 0;
    font-size: 14px;
    color: var(--grey-text);
  }
  .tab {
    position: absolute;
    right: -5px;
    top: 312px;
    width: 13px;
    height: 24px;
    border-radius: 4px 0 0 4px;
    background: var(--blue);
  }

  .contact {
    position: absolute;
    right: 18px;
    bottom: 22px;
    margin: 0;
    padding: 0;
    list-style: none;
    color: var(--white);
    font-size: 15px;
    line-height: 27px;
    white-space: nowrap;
  }
  .contact li { display: flex; justify-content: flex-end; align-items: center; gap: 8px; }
  .contact__label { color: var(--blue); }
  .contact__icon { width: 14px; height: 14px; flex: none; }
  .contact__spacer { width: 14px; flex: none; }
</style>
</head>
<body>
<main class="stage">

  <section class="card card--front" aria-label="Business card front">
    <svg class="card__art" viewBox="0 0 320 550" preserveAspectRatio="none" aria-hidden="true">
      <path d="M0,230 C80,250 120,380 200,410 C260,430 300,425 320,420 L320,550 L0,550 Z" fill="var(--ink)"/>
      <path d="M0,212 C80,232 120,362 200,392 C260,412 300,407 320,402" fill="none" stroke="var(--blue)" stroke-width="6"/>
      <path d="M28,238 C90,262 130,370 200,400" fill="none" stroke="var(--blue)" stroke-width="2"/>
    </svg>

    <div class="brand"><span class="brand__dot"></span><span>TBK Plumbing Services</span></div>

    <div class="holder">
      <p class="holder__name">Rowan Keddle</p>
      <p class="holder__role">Director</p>
    </div>
    <span class="tab"></span>

    <ul class="contact">
      <li><span><span class="contact__label">ABN:</span> 73 215 904 386</span><span class="contact__spacer"></span></li>
      <li>0431 286 517
        <svg class="contact__icon" viewBox="0 0 16 16" aria-hidden="true"><path fill="var(--blue)" d="M3 1h3l1.5 4-2 1.3a9 9 0 0 0 4.2 4.2L11 8.5l4 1.5v3a2 2 0 0 1-2 2A12 12 0 0 1 1 3a2 2 0 0 1 2-2z"/></svg>
      </li>
      <li>rowan@tbk-plumbing.com.au
        <svg class="contact__icon" viewBox="0 0 16 16" aria-hidden="true"><rect x="1" y="3" width="14" height="10" rx="1.5" fill="var(--blue)"/><path d="M2 4l6 5 6-5" fill="none" stroke="var(--ink)" stroke-width="1.5"/></svg>
      </li>
    </ul>
  </section>

  <section class="card card--back" aria-label="Business card back">
    <svg class="card__art" viewBox="0 0 320 550" preserveAspectRatio="none" role="img" aria-label="Faint repeating water-drop pattern on a dark glossy background">
      <defs>
        <linearGradient id="backSheen" x1="0" y1="0" x2="1" y2="1">
          <stop offset="0" stop-color="#262c35"/>
          <stop offset="1" stop-color="#1a1e25"/>
        </linearGradient>
      </defs>
      <rect width="320" height="550" fill="url(#backSheen)"/>
    </svg>
    <div class="brand"><span class="brand__dot"></span><span>TBK Plumbing Services</span></div>
  </section>

</main>
</body>
</html>
```